Design a website for a quickly growing ghostwriting and editing firm

DWB Productions has a website through Wix, but we need help! We are based in Austin, TX, and we work primarily with self-help, wellness, and diet authors. We offer ghostwriting, editing and book development services. You can see our basic site now at www.dorawhitbyproductions.com

```html
<!DOCTYPE html>
<html lang="en">
<head>
<meta charset="utf-8">
<title>DWB Productions</title>
<link href="https://fonts.googleapis.com/css2?family=Roboto:wght@300;400;500;700&display=swap" rel="stylesheet">
<style>
:root{
  --accent:#b5661f;
  --accent-text:#b06a2b;
  --ink:#1c1c1c;
  --body:#555555;
  --muted:#777777;
  --hero-a:#eed9c8;
  --hero-b:#d9b89d;
  --about-bg:#efefed;
  --quote-a:#e6d1c1;
  --quote-b:#d9bba5;
  --city-a:#1a2a3c;
  --city-b:#3b4d5e;
  --footer:#151515;
  --white:#ffffff;
}
*{box-sizing:border-box;margin:0;padding:0}
html,body{width:1200px;height:4260px;overflow:hidden}
body{position:relative;font-family:'Roboto',Arial,sans-serif;color:var(--ink);background:var(--white)}
.abs{position:absolute}

.brand{display:flex;align-items:center;gap:12px;font-weight:500;color:var(--accent-text);white-space:nowrap}
.brand-dot{border-radius:50%;background:var(--accent);flex:none}

.hero{left:0;top:0;width:1200px;height:600px;background:linear-gradient(100deg,var(--hero-a) 0%,#ecd6c3 40%,var(--hero-b) 100%)}
.hero-photo{left:560px;top:50px;width:640px;height:550px;background:linear-gradient(160deg,rgba(120,90,70,.18),rgba(60,70,90,.35))}
.site-header .brand{left:112px;top:18px;font-size:28px}
.nav{right:112px;top:31px;display:flex;gap:49px;font-size:16px;color:var(--ink);white-space:nowrap}
.hero-title{left:112px;top:218px;font-size:45px;font-weight:700;line-height:47px;color:var(--ink);white-space:nowrap}
.hero-text{left:112px;top:326px;width:440px;font-size:13.5px;line-height:24px;font-weight:500;color:#2b2b2b;white-space:nowrap}
.btn{display:flex;align-items:center;justify-content:center;gap:10px;background:var(--accent);color:var(--white);font-weight:500;font-size:15.5px;white-space:nowrap}
.hero .btn{left:112px;top:398px;width:171px;height:48px}
.dots{left:560px;top:557px;display:flex;gap:8px}
.dots span{width:13px;height:13px;border-radius:50%;background:rgba(255,255,255,.55)}
.dots span.on{background:var(--white)}

.sec-title{left:0;width:1200px;font-size:35px;font-weight:500;text-align:center;color:var(--ink)}
.sec-sub{left:0;width:1200px;font-size:15.5px;line-height:26px;text-align:center;color:#333}

.card{width:311px;height:423px;top:795px;background:var(--white);box-shadow:0 2px 10px rgba(0,0,0,.09)}
.card-img{left:0;top:0;width:311px;height:203px}
.img-type{background:linear-gradient(180deg,#e9e9e9,#8c8c8c 60%,#3a3a3a)}
.img-edit{background:linear-gradient(135deg,#c9c4bd,#eeeeee 50%,#b8b3ad)}
.img-book{background:linear-gradient(135deg,#3e5a48,#8c8a7a 55%,#2d3a31)}
.card h3{position:absolute;left:0;top:229px;width:100%;text-align:center;font-size:21px;font-weight:500}
.card p{position:absolute;left:16px;top:264px;width:279px;text-align:center;font-size:13px;line-height:26px;color:var(--body)}
.card .more{position:absolute;left:0;top:378px;width:100%;text-align:center;font-size:15px;font-weight:500;color:var(--accent-text)}
.divider{left:210px;top:1276px;width:780px;height:1px;background:#eeeeee}

.about{left:0;top:1308px;width:1200px;height:591px;background:var(--about-bg)}
.about-photo{left:560px;top:0;width:640px;height:591px;background:linear-gradient(180deg,#d9d5d0,#a8b3c4 55%,#6f7f96)}
.about-frame{left:111px;top:72px;width:590px;height:447px;border:2px solid var(--accent)}
.about .brand{left:147px;top:102px;font-size:34px}
.about h2{left:147px;top:176px;font-size:45px;font-weight:700}
.about h4{left:147px;top:262px;font-size:18px;line-height:30px;font-weight:500;white-space:nowrap}
.about p{left:147px;top:326px;font-size:15px;line-height:28px;color:#444;white-space:nowrap}
.about .btn{left:147px;top:439px;width:170px;height:48px}

.aud{width:320px;top:2116px}
.aud-circle{position:absolute;left:92px;top:0;width:136px;height:136px;border-radius:50%;border:2px solid var(--accent)}
.aud-icon{position:absolute;left:32px;top:32px;width:68px;height:68px;border-radius:50%;background:#f2e3d6}
.aud h3{position:absolute;left:0;top:152px;width:100%;text-align:center;font-size:21px;font-weight:500}
.aud p{position:absolute;left:0;top:189px;width:100%;text-align:center;font-size:13px;line-height:26px;color:var(--muted)}

.books-img{left:132px;top:2480px;width:455px;height:396px;background:linear-gradient(120deg,#e9d2cc,#e8b9b4 55%,#d59b97)}
.eyebrow{font-size:22px;font-weight:400;color:var(--ink)}
.books .eyebrow{left:633px;top:2472px}
.books h2{left:633px;top:2510px;font-size:35px;font-weight:500;white-space:nowrap}
.rule{height:2px;width:52px;background:var(--accent)}
.books .rule{left:635px;top:2560px}
.learn-list{left:633px;top:2584px;list-style:none}
.learn-list li{display:flex;gap:10px;font-size:15.5px;line-height:26px;color:#333;width:460px;height:70px}
.learn-list svg{flex:none;margin-top:7px}

.quotes{left:0;top:2947px;width:1200px;height:676px;background:linear-gradient(180deg,var(--quote-a),var(--quote-b))}
.quotes .sec-title{top:82px}
.tcard{top:149px;width:311px;height:379px;background:var(--white)}
.avatar{position:absolute;left:111px;top:39px;width:89px;height:89px;border-radius:50%;background:linear-gradient(180deg,#c9ced6,#6c7889)}
.tcard h4{position:absolute;top:140px;width:100%;text-align:center;font-size:19px;font-weight:400;color:var(--accent-text)}
.tcard .role{position:absolute;top:168px;width:100%;text-align:center;font-size:14px;color:var(--muted)}
.tcard .q{position:absolute;top:198px;width:100%;text-align:center;font-size:20px;font-style:italic;color:var(--accent-text)}
.tcard p{position:absolute;left:22px;top:238px;width:267px;text-align:center;font-size:14px;line-height:26.5px;color:var(--body)}
.arrows{left:550px;display:flex;gap:16px}

.city{left:0;top:3623px;width:545px;height:563px;background:linear-gradient(180deg,var(--city-a),var(--city-b) 60%,#243021)}
.contact-info{left:296px;top:3818px;color:var(--white)}
.contact-info .lbl{display:flex;align-items:center;gap:6px;font-size:15px;font-weight:700}
.contact-info .phone{font-size:23px;font-weight:500;margin:6px 0 22px;white-space:nowrap}
.contact-info .mail{font-size:15px;font-weight:500;padding-bottom:8px;border-bottom:1px solid rgba(255,255,255,.6);width:232px;white-space:nowrap}
.socials{left:294px;top:3991px;display:flex;gap:8px}
.socials span{width:46px;height:46px;border-radius:50%;background:var(--white)}
.form-area{left:545px;top:3623px;width:655px;height:563px;background:var(--accent)}
.form-area .eyebrow{position:absolute;left:80px;top:80px;color:var(--white);font-size:20px}
.form-area h2{position:absolute;left:80px;top:107px;color:var(--white);font-size:35px;font-weight:500}
.field{position:absolute;border:1px solid rgba(255,255,255,.75);color:var(--white);font-size:13px;display:flex;align-items:flex-start;gap:7px;padding:15px 14px 0}
.submit{position:absolute;left:80px;top:429px;width:149px;height:46px;background:var(--white);color:var(--accent-text);font-size:16px;font-weight:500;display:flex;align-items:center;justify-content:center;gap:10px}
.footer{left:0;top:4186px;width:1200px;height:74px;background:var(--footer);color:#dddddd;font-size:14px;text-align:center;line-height:74px}
</style>
</head>
<body>

<section class="hero abs">
  <div class="hero-photo abs" role="img" aria-label="Smiling writer at a desk typing on a laptop beside an open notebook"></div>
  <header class="site-header">
    <div class="brand abs"><span class="brand-dot" style="width:62px;height:62px"></span>DWB Productions</div>
    <nav class="nav abs"><span>HOME</span><span>ABOUT US</span><span>WHAT WE DO</span><span>BLOG</span><span>CONTACT</span></nav>
  </header>
  <h1 class="hero-title abs">FINIBUS BONORUM<br>ET MALORUM</h1>
  <p class="hero-text abs">Lorem ipsum dolor sit amet, consectetur adipiscing elit, sed do<br>eiusmod tempor incididunt ut labore et dolore magna aliqua.</p>
  <div class="btn abs">GET STARTED
    <svg width="22" height="12" viewBox="0 0 22 12"><path d="M0 6h20M15 1l5 5-5 5" stroke="#fff" stroke-width="1.5" fill="none"/></svg></div>
  <div class="dots abs"><span></span><span class="on"></span><span></span><span></span></div>
</section>

<h2 class="sec-title abs" style="top:676px">WHAT WE OFFER</h2>
<p class="sec-sub abs" style="top:719px">Lorem ipsum dolor sit amet, consectetur adipiscing elit, sed do eiusmod<br>tempor incididunt ut labore et dolore magna</p>

<article class="card abs" style="left:111px">
  <div class="card-img img-type abs" role="img" aria-label="Vintage typewriter with a sheet of paper"></div>
  <h3>GHOST WRITING</h3>
  <p>Lorem ipsum dolor sit aconsectetur adipiscing elit, sed do eiusmod temponcididunt ut labore et dolore magna aliqua. Lorem ipsum dolor sit aconsectetur adipiscing elit</p>
  <div class="more">LEARN MORE &nbsp;»</div>
</article>
<article class="card abs" style="left:443px">
  <div class="card-img img-edit abs" role="img" aria-label="Hand marking up a printed manuscript with a red pen"></div>
  <h3>EDITING</h3>
  <p>Lorem ipsum dolor sit aconsectetur adipiscing elit, sed do eiusmod temponcididunt ut labore et dolore magna aliqua. Lorem ipsum dolor sit aconsectetur adipiscing elit</p>
  <div class="more">LEARN MORE &nbsp;»</div>
</article>
<article class="card abs" style="left:777px">
  <div class="card-img img-book abs" role="img" aria-label="Open book on a desk in front of a chalkboard"></div>
  <h3>BOOK DEVELOPMENT</h3>
  <p>Lorem ipsum dolor sit aconsectetur adipiscing elit, sed do eiusmod temponcididunt ut labore et dolore magna aliqua. Lorem ipsum dolor sit aconsectetur adipiscing elit</p>
  <div class="more">LEARN MORE &nbsp;»</div>
</article>
<div class="divider abs"></div>

<section class="about abs">
  <div class="about-photo abs" role="img" aria-label="Smiling man in glasses and a checked shirt holding a laptop"></div>
  <div class="about-frame abs"></div>
  <div class="brand abs"><span class="brand-dot" style="width:66px;height:66px"></span>DWB Productions</div>
  <h2 class="abs">ABOUT US</h2>
  <h4 class="abs">Section 1.10.32 of "de Finibus Bonorum et<br>Malorum", written by Cicero in 45 BC</h4>
  <p class="abs">Lorem ipsum dolor sit amet, consectetur adipiscing elit, sed<br>do eiusmod tempor incididunt ut labort dolore magna aliqua.<br>Quis ipsum suspendisse ultrices gravida</p>
  <div class="btn abs">LEARN MORE
    <svg width="22" height="12" viewBox="0 0 22 12"><path d="M0 6h20M15 1l5 5-5 5" stroke="#fff" stroke-width="1.5" fill="none"/></svg></div>
</section>

<h2 class="sec-title abs" style="top:1975px">WE WORK PRIMARILY WITH</h2>
<p class="sec-sub abs" style="top:2023px">Lorem ipsum dolor sit amet, consectetur adipiscing elit, sed do eiusmod<br>tempor incididunt ut labore et dolore magna</p>

<div class="aud abs" style="left:101px">
  <div class="aud-circle"><div class="aud-icon" role="img" aria-label="Self-help line icon"></div></div>
  <h3>SELF-HELP</h3>
  <p>Lorem ipsum dolor sit amet, consectur adipiscing elit, sed do eiusmod tempor incididunt ut labore et dolore magna aliqua.</p>
</div>
<div class="aud abs" style="left:440px">
  <div class="aud-circle"><div class="aud-icon" role="img" aria-label="Lotus wellness line icon"></div></div>
  <h3>WELLNESS</h3>
  <p>Lorem ipsum dolor sit amet, consectur adipiscing elit, sed do eiusmod tempor incididunt ut labore et dolore magna aliqua.</p>
</div>
<div class="aud abs" style="left:777px">
  <div class="aud-circle"><div class="aud-icon" role="img" aria-label="Diet author line icon"></div></div>
  <h3>DIET AUTHORS</h3>
  <p>Lorem ipsum dolor sit amet, consectur adipiscing elit, sed do eiusmod tempor incididunt ut labore et dolore magna aliqua.</p>
</div>

<section class="books">
  <div class="books-img abs" role="img" aria-label="Open book spread with a portrait and a pink cover showing a sneaker"></div>
  <div class="eyebrow abs">ABOUT THE BOOKS</div>
  <h2 class="abs">HERE’S WHAT YOU’LL LEARN</h2>
  <div class="rule abs"></div>
  <ul class="learn-list abs">
    <li><svg width="22" height="12" viewBox="0 0 22 12"><path d="M0 6h20M15 1l5 5-5 5" stroke="#b5661f" stroke-width="1.5" fill="none"/></svg>Lorem ipsum dolor sit amet, consectetur adipiscing elit, sed do eiusmod tempor incididunt ut labore</li>
    <li><svg width="22" height="12" viewBox="0 0 22 12"><path d="M0 6h20M15 1l5 5-5 5" stroke="#b5661f" stroke-width="1.5" fill="none"/></svg>Lorem ipsum dolor sit amet, consectetur adipiscing elit, sed do eiusmod tempor incididunt ut labore</li>
    <li><svg width="22" height="12" viewBox="0 0 22 12"><path d="M0 6h20M15 1l5 5-5 5" stroke="#b5661f" stroke-width="1.5" fill="none"/></svg>Lorem ipsum dolor sit amet, consectetur adipiscing elit, sed do eiusmod tempor incididunt ut labore</li>
    <li><svg width="22" height="12" viewBox="0 0 22 12"><path d="M0 6h20M15 1l5 5-5 5" stroke="#b5661f" stroke-width="1.5" fill="none"/></svg>Lorem ipsum dolor sit amet, consectetur adipiscing elit, sed do eiusmod tempor incididunt ut labore</li>
  </ul>
</section>

<section class="quotes abs">
  <h2 class="sec-title abs">WHAT PEOPLES ARE SAYING</h2>
  <article class="tcard abs" style="left:111px">
    <div class="avatar" role="img" aria-label="Client portrait"></div>
    <h4>JOHN SMITH</h4><div class="role">At vero eos et accusamus</div>
    <div class="q">"Sed ut perspiciatis unde"</div>
    <p>Lorem ipsum dolor sitmet, consectetur adipiscing elit, sed do eiusmod tempor incididunt ut labodolore magna aliqua. Quis ipsum suspendisse</p>
  </article>
  <article class="tcard abs" style="left:445px">
    <div class="avatar" role="img" aria-label="Client portrait"></div>
    <h4>JOHN SMITH</h4><div class="role">At vero eos et accusamus</div>
    <div class="q">"Sed ut perspiciatis unde"</div>
    <p>Lorem ipsum dolor sitmet, consectetur adipiscing elit, sed do eiusmod tempor incididunt ut labodolore magna aliqua. Quis ipsum suspendisse</p>
  </article>
  <article class="tcard abs" style="left:778px">
    <div class="avatar" role="img" aria-label="Client portrait"></div>
    <h4>JOHN SMITH</h4><div class="role">At vero eos et accusamus</div>
    <div class="q">"Sed ut perspiciatis unde"</div>
    <p>Lorem ipsum dolor sitmet, consectetur adipiscing elit, sed do eiusmod tempor incididunt ut labodolore magna aliqua. Quis ipsum suspendisse</p>
  </article>
  <div class="arrows abs" style="top:565px">
    <svg width="42" height="22" viewBox="0 0 42 22"><path d="M41 11H2M11 2l-9 9 9 9" stroke="#1c1c1c" stroke-width="2" fill="none"/></svg>
    <svg width="42" height="22" viewBox="0 0 42 22"><path d="M1 11h39M31 2l9 9-9 9" stroke="#1c1c1c" stroke-width="2" fill="none"/></svg>
  </div>
</section>

<div class="city abs" role="img" aria-label="City skyline at dusk with lit towers above the river trees"></div>
<div class="contact-info abs">
  <div class="lbl"><svg width="17" height="17" viewBox="0 0 24 24"><path d="M6.6 10.8a15 15 0 006.6 6.6l2.2-2.2a1 1 0 011-.25 11.4 11.4 0 003.6.57 1 1 0 011 1V20a1 1 0 01-1 1A17 17 0 013 4a1 1 0 011-1h3.5a1 1 0 011 1 11.4 11.4 0 00.57 3.6 1 1 0 01-.25 1z" fill="#fff"/></svg>CALL:</div>
  <div class="phone">(512) 555-0148</div>
  <div class="lbl"><svg width="18" height="14" viewBox="0 0 18 14"><rect x="0.5" y="0.5" width="17" height="13" fill="#fff"/><path d="M1 1l8 7 8-7" stroke="#2a3a4c" stroke-width="1.4" fill="none"/></svg>EMAIL:</div>
  <div class="mail">info@dwbstudio.net</div>
</div>
<div class="socials abs"><span></span><span></span><span></span></div>

<section class="form-area abs">
  <div class="eyebrow">CONTACT</div>
  <h2>GET IN TOUCH</h2>
  <div class="field" style="left:80px;top:182px;width:231px;height:48px">
    <svg width="12" height="13" viewBox="0 0 12 13"><circle cx="6" cy="3.5" r="3" fill="#fff"/><path d="M0 13a6 5 0 0112 0z" fill="#fff"/></svg>Your Name*</div>
  <div class="field" style="left:328px;top:182px;width:231px;height:48px">
    <svg width="12" height="13" viewBox="0 0 12 13"><circle cx="6" cy="3.5" r="3" fill="#fff"/><path d="M0 13a6 5 0 0112 0z" fill="#fff"/></svg>Last Name*</div>
  <div class="field" style="left:80px;top:245px;width:231px;height:48px">
    <svg width="13" height="13" viewBox="0 0 13 13"><path d="M13 0L0 6l5 2 2 5z" fill="#fff"/></svg>Your Email*</div>
  <div class="field" style="left:328px;top:245px;width:231px;height:48px">
    <svg width="13" height="13" viewBox="0 0 24 24"><path d="M6.6 10.8a15 15 0 006.6 6.6l2.2-2.2a1 1 0 011-.25 11.4 11.4 0 003.6.57 1 1 0 011 1V20a1 1 0 01-1 1A17 17 0 013 4a1 1 0 011-1h3.5a1 1 0 011 1 11.4 11.4 0 00.57 3.6 1 1 0 01-.25 1z" fill="#fff"/></svg>Your Phone*</div>
  <div class="field" style="left:80px;top:308px;width:479px;height:102px">
    <svg width="13" height="13" viewBox="0 0 13 13"><rect x="0.5" y="2.5" width="10" height="10" stroke="#fff" fill="none"/><path d="M5 8l7-7" stroke="#fff" stroke-width="1.5"/></svg>Your Message*</div>
  <div class="submit">SUBMIT
    <svg width="22" height="12" viewBox="0 0 22 12"><path d="M0 6h20M15 1l5 5-5 5" stroke="#b06a2b" stroke-width="1.5" fill="none"/></svg></div>
</section>

<footer class="footer abs">Copyright © 2021DWBPRODUCTIONS. All rights reserved.</footer>

</body>
</html>
```